Kestrel Facilities Business Card Design

We would now like to design business cards with the new Kestrel Facilities logo

Target Market(s)

Professional

Industry/Entity Type

Professional services

Contact Information for Business Card

Employee name, title, phone number, email address, corporate office address and logo.

Font styles to use
Sans Serif

Colors
0054AA
0677BA
7BADD7
CADEEF
E8F1F8

Requirements
Must have
• My logo
Should not have
• any other pictures or images besides my logo

```html
<!DOCTYPE html>
<html lang="en">
<head>
<meta charset="utf-8">
<title>Kestrel Facilities – Business Card</title>
<link rel="stylesheet" href="https://fonts.googleapis.com/css2?family=Montserrat:wght@400;500;700&display=swap">
<style>
  :root {
    --brand-blue: #367cc0;
    --ink: #2b2b2b;
    --paper: #ffffff;
    --backdrop: #e9e9e9;
  }
  * { box-sizing: border-box; margin: 0; padding: 0; }
  html, body {
    width: 1200px; height: 1028px; overflow: hidden;
    background: var(--backdrop);
    font-family: "Montserrat", Arial, sans-serif;
  }
  .card {
    position: absolute; left: 310px; width: 579px; height: 331px;
    border-radius: 24px; overflow: hidden;
    box-shadow: 0 3px 8px rgba(0,0,0,0.18);
  }
  .card--front { top: 165px; background: var(--paper); }
  .card--back { top: 532px; background: var(--brand-blue);
    display: flex; align-items: center; justify-content: center; }

  .holder { position: absolute; left: 42px; top: 36px; }
  .holder__name { font-size: 20px; font-weight: 700; color: var(--brand-blue); line-height: 1.2; }
  .holder__title { font-size: 14px; font-weight: 400; color: var(--ink); margin-top: 1px; }

  .website { position: absolute; left: 42px; top: 145px; font-size: 13.5px; color: var(--ink); letter-spacing: 0.2px; }

  .contact-band {
    position: absolute; left: 0; top: 178px; width: 359px; height: 111px;
    background: var(--brand-blue); color: var(--paper);
    padding: 11px 0 0 42px; font-size: 14px; line-height: 19.5px;
  }
  .contact-band__row { display: flex; align-items: center; gap: 8px; }
  .contact-band__row svg { width: 12px; height: 12px; flex: none; }
  .contact-band__address { margin-top: 11px; }

  .wordmark {
    color: var(--brand-blue); font-weight: 700; text-transform: uppercase;
    line-height: 1.02; letter-spacing: 1px;
  }
  .wordmark--front { position: absolute; left: 370px; top: 178px; width: 167px; height: 111px;
    display: flex; flex-direction: column; justify-content: center; font-size: 26px; }
  .wordmark--back { color: var(--paper); font-size: 42px; text-align: center; }
</style>
</head>
<body>
  <section class="card card--front" aria-label="Business card front">
    <div class="holder">
      <p class="holder__name">Daniel Hargrove</p>
      <p class="holder__title">Director</p>
    </div>
    <p class="website">www.kestrelfacilities.com</p>

    <div class="contact-band">
      <p class="contact-band__row">
        <svg viewBox="0 0 12 12" aria-hidden="true"><path d="M3 1.2 L4.6 3.6 L3.6 4.6 C4.2 6.2 5.6 7.7 7.4 8.4 L8.4 7.4 L10.8 9 L9.8 10.8 C5.6 10.6 1.4 6.4 1.2 2.2 Z" fill="none" stroke="#fff" stroke-width="1.1" stroke-linejoin="round"/></svg>
        (541) 555-0148
      </p>
      <p class="contact-band__row">
        <svg viewBox="0 0 12 12" aria-hidden="true"><rect x="1" y="2.5" width="10" height="7" fill="none" stroke="#fff" stroke-width="1.1"/><path d="M1 2.8 L6 6.6 L11 2.8" fill="none" stroke="#fff" stroke-width="1.1"/></svg>
        info@kestrelfacilities.com
      </p>
      <p class="contact-band__address">1187 Larkspur Lane<br>Corvallis, OR 97330</p>
    </div>

    <div class="wordmark wordmark--front"><span>Kestrel</span><span>Facilities</span></div>
  </section>

  <section class="card card--back" aria-label="Business card back">
    <div class="wordmark wordmark--back">Kestrel<br>Facilities</div>
  </section>
</body>
</html>
```